Marlow Estate Fixers (Handyman / Home Improvement Company)

Looking for a double sided professional looking business card with Logo attached to be highlighted on one side and throwing in an image of a handyman as an option would be nice to see as well. We are a company focused on providing quality Handyman and Home improvement services in a timely manner that is done right the first time with integrity

Industry/Entity Type

Handyman / Home Improvement

Contact Information for Business Card

(LOGO, Name, Mobile and office phone numbers, email) on front side of card, (the words "The SOLUTION to all of your Handyman and Home Improvement needs" followed by "Family Owned and Operated" at the very bottom) on the back.

Colors
EB3D1F
EC4F4E
F09395
F8D3D4
FCEDEE

Requirements
Must have
• Red, Gray, Black Color scheme
Should not have
• No Yellow or Blue colors

```html
<!DOCTYPE html>
<html lang="en">
<head>
<meta charset="utf-8">
<title>Marlow Estate Fixers – Business Card</title>
<link rel="stylesheet" href="https://fonts.googleapis.com/css2?family=Anton&family=Montserrat:wght@400;600;700;800&display=swap">
<style>
  :root {
    --red: #e62b2f;
    --red-deep: #c9262a;
    --ink: #1e1e1e;
    --graphite: #3a3a3c;
    --paper: #ffffff;
    --backdrop: #262626;
    --figure-blue: #b8474c;
    --figure-shade: #8e2a2e;
  }
  * { margin: 0; padding: 0; box-sizing: border-box; }
  html, body {
    width: 1200px; height: 1059px; overflow: hidden;
    background: var(--backdrop);
    font-family: "Montserrat", sans-serif;
  }
  .canvas { position: relative; width: 1200px; height: 1059px; }

  .card {
    position: absolute; left: 262px; width: 715px; height: 409px;
    border-radius: 26px; overflow: hidden;
  }

  /* Front */
  .card--front { top: 95px; background: var(--paper); }
  .brand {
    position: absolute; left: 0; right: 0; top: 120px;
    display: flex; justify-content: center; align-items: center; gap: 14px;
  }
  .brand__dot { width: 18px; height: 18px; border-radius: 50%; background: var(--red); }
  .brand__name {
    font-weight: 800; font-size: 38px; color: var(--red);
    letter-spacing: 0.5px; text-transform: uppercase;
  }
  .person { position: absolute; right: calc(715px - 328px); top: 284px; text-align: right; }
  .person__name { font-weight: 700; font-size: 28px; color: var(--red); line-height: 1; white-space: nowrap; }
  .person__role { margin-top: 12px; font-size: 19px; color: var(--ink); line-height: 1; }
  .divider {
    position: absolute; left: 356px; top: 267px; width: 2px; height: 94px;
    background: linear-gradient(to bottom, transparent, var(--red) 15%, var(--red) 85%, transparent);
  }
  .contacts { position: absolute; left: 383px; top: 268px; list-style: none; }
  .contacts li { display: flex; align-items: center; height: 31px; font-size: 19.5px; color: var(--ink); }
  .contacts svg { width: 22px; height: 22px; margin-right: 12px; flex: none; }
  .band { position: absolute; left: 0; bottom: 0; width: 715px; height: 12px; display: block; }

  /* Back */
  .card--back { top: 529px; background: var(--red); color: var(--paper); }
  .slogan { position: absolute; left: 20px; width: 400px; top: 90px; text-align: center; }
  .slogan__lead { font-weight: 700; font-size: 29px; line-height: 1; white-space: nowrap; }
  .slogan__big {
    font-family: "Anton", sans-serif; font-size: 44px; line-height: 1.27;
    transform: scaleX(0.92); white-space: nowrap; margin-top: 10px;
  }
  .slogan__big .small { font-size: 38px; }
  .tagline {
    position: absolute; left: 20px; width: 400px; bottom: 26px;
    text-align: center; font-weight: 700; font-size: 22.5px; white-space: nowrap;
  }
  .mascot {
    position: absolute; left: 438px; top: 18px; width: 275px; height: 380px;
    border-radius: 20px 20px 60px 60px;
    background: linear-gradient(180deg, var(--figure-blue) 0%, var(--figure-shade) 100%);
    opacity: 0.55;
  }
</style>
</head>
<body>
<main class="canvas">

  <section class="card card--front">
    <div class="brand">
      <span class="brand__dot"></span>
      <span class="brand__name">Marlow Estate Fixers</span>
    </div>

    <div class="person">
      <p class="person__name">Daniel Hartley</p>
      <p class="person__role">Owner</p>
    </div>

    <div class="divider"></div>

    <ul class="contacts">
      <li>
        <svg viewBox="0 0 24 24" aria-hidden="true"><rect x="6" y="2" width="12" height="20" rx="2" fill="none" stroke="#e62b2f" stroke-width="2"/><rect x="8" y="5" width="8" height="11" fill="#e62b2f"/><circle cx="12" cy="19" r="1.2" fill="#e62b2f"/></svg>
        044-555 018 234
      </li>
      <li>
        <svg viewBox="0 0 24 24" aria-hidden="true"><path d="M3 9c0-3 4-5 9-5s9 2 9 5v1.5h-4.5V8.5h-9v2H3z" fill="#e62b2f"/><path d="M6 12h12l2 8H4z" fill="#e62b2f"/><circle cx="12" cy="16" r="2" fill="#fff"/></svg>
        044-555 018 235
      </li>
      <li>
        <svg viewBox="0 0 24 24" aria-hidden="true"><rect x="2" y="5" width="20" height="14" fill="#e62b2f"/><path d="M2 5l10 8 10-8" fill="none" stroke="#fff" stroke-width="1.8"/></svg>
        hello@marlowfixers.com
      </li>
    </ul>

    <svg class="band" viewBox="0 0 715 12" preserveAspectRatio="none" aria-hidden="true">
      <polygon points="0,0 353,0 357,12 0,12" fill="var(--red)"/>
      <polygon points="353,0 359,0 363,12 357,12" fill="#ffffff"/>
      <polygon points="359,0 715,0 715,12 363,12" fill="var(--graphite)"/>
    </svg>
  </section>

  <section class="card card--back">
    <div class="slogan">
      <p class="slogan__lead">Your SOLUTION to all of</p>
      <p class="slogan__big"><span class="small">your</span> Handyman <span class="small">and</span><br>Home Improvement<br>Needs</p>
    </div>
    <p class="tagline">Family Owned and Operated</p>
    <div class="mascot" role="img" aria-label="Cartoon handyman in work overalls holding a pipe wrench and a spanner"></div>
  </section>

</main>
</body>
</html>
```